we can communicate on this, but i want to follow the approach we took on Pellew|Marsh & Quinlan but i feel the card front needs the black background and the platinum and gold logo. The back? I am open. we can use the same info from PM&Q. Velmont Arc is an enhanced equity investment fund - basically a very exclusive boutique hedge fund that uses only stock options. very advanced things. hope you are interested

Contact Information for Business Card

Dr. Lewis T. Brennick, CFA
Scientifique de fusée financière
701.555.0143
LTBquant47@mailvantor.com

4718 Willow Creek Bend W.
West Fargo, ND 58078

No web site

Colors

Designer to choose colors to be used in the design.

Requirements
Nice to have
• I tend to prefer the most visible applications of the logo to include logo and name, the logo version with a black background and the gold and platinum components separated by the black. I see this working well for a single side (logo and name - this is card front to me).
• I am fairly open to other treatments on the reverse side with the data. To me, it makes sense to have a different color rendition of the logo on the reverse and it may be a muted black tone on tone or an oversized portion that would have spot UV. Or, the reverse may play with colors and layout
Should not have
• Other colors = no no
• Decorative font

```html
<!DOCTYPE html>
<html lang="en">
<head>
<meta charset="utf-8">
<title>Velmont Arc — Business Card</title>
<link rel="stylesheet" href="https://fonts.googleapis.com/css2?family=Montserrat:wght@400;500;700&display=swap">
<style>
  :root {
    --backdrop: #1b1c1f;
    --card: #23262a;
    --card-deep: #15171a;
    --tone: #34373c;
    --white: #f2f2f2;
    --gold: #c9a235;
    --text-soft: #d7d7d7;
  }
  * { margin: 0; padding: 0; box-sizing: border-box; }
  html, body { width: 1200px; height: 800px; overflow: hidden; }
  body {
    background: var(--backdrop);
    font-family: "Montserrat", sans-serif;
    position: relative;
  }
  .card {
    position: absolute;
    width: 520px;
    height: 297px;
    border-radius: 18px;
    background: var(--card);
    box-shadow: 0 18px 40px rgba(0,0,0,.45);
    overflow: hidden;
  }

  /* Reverse: tone-on-tone brand */
  .card--reverse { left: 80px; top: 90px; background: var(--card-deep); }
  .reverse-brand {
    position: absolute;
    right: 40px; top: 44px;
    display: flex; align-items: center; gap: 14px;
  }
  .reverse-brand .brand-dot {
    width: 44px; height: 44px; border-radius: 50%;
    background: var(--tone);
  }
  .reverse-brand .brand-name {
    font-weight: 700; font-size: 26px; letter-spacing: 2px;
    color: var(--tone);
  }

  /* Front: brand + contact */
  .card--front { left: 600px; top: 410px; }
  .front-brand {
    position: absolute;
    left: 20px; top: 0; bottom: 0;
    width: 230px;
    display: flex; flex-direction: column;
    align-items: center; justify-content: center; gap: 14px;
  }
  .front-brand .brand-dot {
    width: 60px; height: 60px; border-radius: 50%;
    background: var(--gold);
  }
  .front-brand .brand-name {
    font-weight: 700; font-size: 22px; letter-spacing: 1.5px;
    color: var(--white);
    white-space: nowrap;
  }
  .divider {
    position: absolute;
    left: 262px; top: 42px;
    width: 1px; height: 212px;
    background: var(--gold);
  }
  .contact {
    position: absolute;
    left: 278px; top: 0; bottom: 0;
    width: 228px;
    display: flex; flex-direction: column; justify-content: center;
    color: var(--text-soft);
  }
  .contact-name {
    font-weight: 700; font-size: 12.5px; letter-spacing: .2px;
    color: var(--white);
    white-space: nowrap;
  }
  .contact-role {
    font-weight: 500; font-size: 11px;
    color: var(--gold);
    margin-top: 3px;
  }
  .contact-address {
    font-size: 11px; line-height: 1.5;
    margin-top: 16px;
  }
  .contact-list { list-style: none; margin-top: 12px; }
  .contact-list li {
    display: flex; align-items: center; gap: 8px;
    font-size: 11px; line-height: 1.9;
    white-space: nowrap;
  }
  .contact-list svg { width: 11px; height: 11px; flex: none; }
</style>
</head>
<body>

  <section class="card card--reverse" aria-label="Card reverse">
    <div class="reverse-brand">
      <span class="brand-dot"></span>
      <span class="brand-name">VELMONT ARC</span>
    </div>
  </section>

  <section class="card card--front" aria-label="Card front">
    <div class="front-brand">
      <span class="brand-dot"></span>
      <span class="brand-name">VELMONT ARC</span>
    </div>

    <div class="divider"></div>

    <div class="contact">
      <p class="contact-name">DR. LEWIS T. BRENNICK, CFA</p>
      <p class="contact-role">Scientifique de fusée financière</p>
      <p class="contact-address">4718 Willow Creek Bend W.<br>West Fargo, ND 58078</p>
      <ul class="contact-list">
        <li>
          <svg viewBox="0 0 12 12" aria-hidden="true"><path d="M2.5 1 L4.5 1 L5.3 3.4 L4 4.4 C4.6 5.8 6.2 7.4 7.6 8 L8.6 6.7 L11 7.5 L11 9.5 C11 10.3 10.3 11 9.5 11 C5 11 1 7 1 2.5 C1 1.7 1.7 1 2.5 1 Z" fill="var(--gold)"/></svg>
          701.555.0143
        </li>
        <li>
          <svg viewBox="0 0 12 12" aria-hidden="true"><rect x="1" y="2.5" width="10" height="7" fill="var(--gold)"/><path d="M1 2.5 L6 6.5 L11 2.5" stroke="var(--card)" stroke-width="1" fill="none"/></svg>
          LTBquant47@mailvantor.com
        </li>
      </ul>
    </div>
  </section>

</body>
</html>
```